Corporate Travel Technology Company needs new Business Card design

We need a new business card design to reflect our re-branded company. Our company is called tolvEn (pronounced tolvenn) and we provide Business Intelligence and mobile travel management solutions for the corporate travel industry. Our multinational customers use our solutions to manage large travel budgets and frequent travellers, as well as to save money and reduce risk. We'd like to see designs that use the blue and green palette as well as our corporate logo (attached below). The design should communicate innovation, insight, forward thinking, contemporary, trusted.

Target Market(s)

Large multinational corporates and Travel Agencies.

Industry/Entity Type

Business

Contact Information for Business Card

Rosalind Mercer
Chief Executive
tolvEn
Phone number - +61 (0)2 8134 2907
Email address - rosalind.mercer@tolven-example.com
Mobile number - +61 (0)438 516 702
www.tolven-example.com

Font styles to use
Other font styles liked:
• Please use font as close to corporate logo as possible

Colors
0255a3
0393ce
00a990
33b8a4
33a6d7
3176b5

Requirements
Must have
• Please include the words;
• Mobile Travel Management
• Accelerating Travel Business Insights
• Use corporate logo - although icon can be stylised if needed

```html
<!DOCTYPE html>
<html lang="en">
<head>
<meta charset="utf-8">
<title>tolvEn business card</title>
<link rel="stylesheet" href="https://fonts.googleapis.com/css2?family=Open+Sans:wght@400;600;700&display=swap">
<style>
  :root {
    --page-bg: #eef1f4;
    --card-bg: #ffffff;
    --brand-blue: #0393ce;
    --brand-blue-light: #33a6d7;
    --brand-blue-deep: #0255a3;
    --ink-dark: #3e4b50;
    --ink-grey: #6b7478;
    --card-shadow: 0 6px 18px rgba(20, 40, 60, 0.18);
  }
  html, body {
    margin: 0;
    width: 1200px;
    height: 913px;
    overflow: hidden;
    background: var(--page-bg);
    font-family: "Open Sans", Arial, sans-serif;
  }
  .canvas {
    position: relative;
    width: 1200px;
    height: 913px;
  }
  .card {
    position: absolute;
    top: 298px;
    width: 520px;
    height: 316px;
    background: var(--card-bg);
    border-radius: 18px;
    box-shadow: var(--card-shadow);
    overflow: hidden;
  }
  .card--front { left: 50px; }
  .card--back { left: 630px; }

  /* Front */
  .front__disc {
    position: absolute;
    left: -150px;
    top: 40px;
    width: 360px;
    height: 360px;
    border-radius: 50%;
    background: linear-gradient(160deg, var(--brand-blue-light), var(--brand-blue) 55%, var(--brand-blue-deep));
  }
  .front__contact {
    position: absolute;
    right: 34px;
    top: 38px;
    text-align: right;
    color: var(--brand-blue);
  }
  .contact__name {
    margin: 0;
    font-size: 23px;
    font-weight: 700;
    line-height: 1.1;
  }
  .contact__title {
    margin: 2px 0 30px;
    font-size: 14px;
    color: var(--ink-grey);
  }
  .contact__list {
    list-style: none;
    margin: 0;
    padding: 0;
    font-size: 14px;
    line-height: 22px;
  }
  .contact__list li {
    display: flex;
    justify-content: flex-end;
    align-items: center;
    gap: 6px;
  }
  .contact__icon {
    width: 12px;
    height: 12px;
    flex: none;
    stroke: var(--ink-grey);
    fill: none;
    stroke-width: 1.4;
  }

  /* Back */
  .back__brand {
    position: absolute;
    left: 0;
    right: 0;
    top: 78px;
    display: flex;
    justify-content: center;
    align-items: center;
    gap: 14px;
  }
  .brand__dot {
    width: 26px;
    height: 26px;
    border-radius: 50%;
    background: var(--brand-blue-light);
  }
  .brand__name {
    font-size: 86px;
    font-weight: 600;
    color: var(--ink-dark);
    letter-spacing: -1px;
    line-height: 1;
  }
  .back__taglines {
    position: absolute;
    left: 62px;
    top: 214px;
    list-style: none;
    margin: 0;
    padding: 0;
    font-size: 15px;
    line-height: 20px;
    color: var(--ink-dark);
  }
  .back__taglines li {
    display: flex;
    align-items: center;
    gap: 8px;
  }
  .tagline__mark {
    width: 8px;
    height: 8px;
    background: var(--brand-blue-light);
  }
</style>
</head>
<body>
<main class="canvas">
  <section class="card card--front" aria-label="Card front">
    <div class="front__disc"></div>
    <div class="front__contact">
      <h1 class="contact__name">Rosalind Mercer</h1>
      <p class="contact__title">Chief Executive</p>
      <ul class="contact__list">
        <li>+61 (0)438 516 702
          <svg class="contact__icon" viewBox="0 0 12 12" aria-hidden="true"><rect x="3" y="1" width="6" height="10" rx="1"/></svg></li>
        <li>+61 (0)2 8134 2907
          <svg class="contact__icon" viewBox="0 0 12 12" aria-hidden="true"><path d="M2 2c0 5 3 8 8 8l0-2-2-1-1 1C5 7 5 7 4 5l1-1-1-2z"/></svg></li>
        <li>www.tolven-example.com
          <svg class="contact__icon" viewBox="0 0 12 12" aria-hidden="true"><circle cx="6" cy="6" r="4.8"/><path d="M1.2 6h9.6M6 1.2c-2.5 3-2.5 6.6 0 9.6M6 1.2c2.5 3 2.5 6.6 0 9.6"/></svg></li>
        <li>rosalind.mercer@tolven-example.com
          <svg class="contact__icon" viewBox="0 0 12 12" aria-hidden="true"><rect x="1" y="2.5" width="10" height="7"/><path d="M1 2.5l5 4 5-4"/></svg></li>
      </ul>
    </div>
  </section>

  <section class="card card--back" aria-label="Card back">
    <div class="back__brand">
      <span class="brand__dot"></span>
      <span class="brand__name">tolvEn</span>
    </div>
    <ul class="back__taglines">
      <li><span class="tagline__mark"></span>Mobile Travel Management</li>
      <li><span class="tagline__mark"></span>Accelerating Travel Business Insights</li>
    </ul>
  </section>
</main>
</body>
</html>
```